Natural healthcare clinic needs stationery and business card design

We have had a logo developed by Pixel Harbor and are now looking at utilising it for a new business concept. The concept is a natural healthcare clinic that hosts a number of small businesses. The individual practitioners may want to utilise the host business stationery to provide a consistent message to clients.

I am looking for a stationery design - letterhead, DL brochure template and business card that uses our logo. The business name 'Bright Meadows' is all about getting rhythm back into your life so you can be fit and healthy. The stationery design should reflect this.

There are a couple of requirements for the business card, it needs to be double-sided with black and white back. There should be lines to write appointment times on. The cards may need to be custom named on the front for example Carol Fenwick, Remedial Therapist and Aromatherapist. Therefore if a template can be provided so we can customise this information using MS Publisher, it would be appreciated.

The DL brochure template needs to be A4 folded to DL. I am looking for a consistent brand message that can be utilised to produce our own clinic brochures.

The natural healthcare clinic will host the following types of businesses - remedial massage, pregnancy massage, oncology massage, aromatherapy, acupuncture - as a bit of a guide.

Target Market(s)

25-45 year old male and females who work full time.

Industry/Entity Type

Healthcare

Requirements
Must have
• Use the logo I have already.

```html
<!DOCTYPE html>
<html lang="en">
<head>
<meta charset="utf-8">
<title>Bright Meadows – Business Card</title>
<link href="https://fonts.googleapis.com/css2?family=Open+Sans:wght@300;400;600&display=swap" rel="stylesheet">
<style>
  :root {
    --page-bg: #e9e5dc;
    --card-white: #ffffff;
    --olive-dark: #2f3a06;
    --olive-light: #6f8c1e;
    --lime: #9cc43a;
    --peach: #f4b98c;
    --text-olive: #5a6a1c;
    --text-grey: #4a4a4a;
    --ink: #111111;
    --ink-soft: #555555;
    --rule: #222222;
  }
  * { margin: 0; padding: 0; box-sizing: border-box; }
  html, body { width: 1200px; height: 1024px; overflow: hidden; }
  body {
    background: var(--page-bg);
    font-family: "Open Sans", Arial, sans-serif;
    position: relative;
  }
  .card {
    position: absolute;
    left: 200px;
    width: 800px;
    height: 457px;
    border-radius: 36px;
    overflow: hidden;
    box-shadow: 0 6px 18px rgba(0,0,0,0.18);
    background: var(--card-white);
  }
  /* ---------- Front ---------- */
  .card-front { top: 40px; }
  .front-swoosh { position: absolute; inset: 0; width: 100%; height: 100%; }
  .front-brand {
    position: absolute;
    left: 50px; top: 180px;
    display: flex; align-items: center; gap: 14px;
  }
  .brand-dot {
    width: 20px; height: 20px; border-radius: 50%;
    background: var(--lime);
  }
  .front-brand .brand-name {
    font-size: 38px; font-weight: 400; color: var(--text-olive);
    letter-spacing: -0.5px;
  }
  .divider {
    position: absolute;
    left: 425px; top: 70px;
    width: 2px; height: 210px;
    background: linear-gradient(to bottom, rgba(111,140,30,0), var(--olive-light) 40%, rgba(111,140,30,0));
  }
  .contact {
    position: absolute;
    left: 450px; top: 62px;
    color: var(--text-grey);
  }
  .contact .person {
    font-size: 21px; color: var(--text-olive); font-weight: 400;
    margin-bottom: 20px;
  }
  .contact .person .job { color: var(--lime); font-weight: 600; font-size: 17px; }
  .contact .address { font-size: 15px; line-height: 22px; margin-bottom: 18px; }
  .contact ul { list-style: none; font-size: 15px; line-height: 24px; }
  .contact li { display: flex; align-items: center; gap: 10px; }
  .contact svg { width: 14px; height: 14px; flex: none; }
  .front-web {
    position: absolute;
    left: 70px; bottom: 22px;
    font-size: 15px; color: #ffffff; letter-spacing: 0.3px;
  }
  /* ---------- Back (black and white) ---------- */
  .card-back { top: 527px; border: 2px solid var(--rule); }
  .back-brand {
    position: absolute;
    left: 0; right: 0; top: 42px;
    display: flex; justify-content: center; align-items: center; gap: 14px;
  }
  .back-brand .brand-dot { background: var(--ink); width: 16px; height: 16px; }
  .back-brand .brand-name {
    font-size: 40px; font-weight: 300; color: var(--ink); letter-spacing: -0.5px;
  }
  .back-web {
    position: absolute;
    left: 0; right: 0; top: 104px;
    text-align: center;
    font-size: 15px; color: var(--ink-soft); letter-spacing: 0.4px;
  }
  .appointments {
    position: absolute;
    left: 70px; right: 70px; top: 160px;
  }
  .appointments h2 {
    font-size: 17px; font-weight: 600; color: var(--ink);
    text-transform: uppercase; letter-spacing: 2px;
    text-align: center; margin-bottom: 14px;
  }
  .appt-row {
    display: flex; gap: 30px; align-items: flex-end;
    height: 52px;
  }
  .appt-field {
    display: flex; align-items: flex-end; gap: 10px;
    font-size: 15px; color: var(--ink);
  }
  .appt-field.date { flex: 3; }
  .appt-field.time { flex: 2; }
  .appt-line {
    flex: 1; height: 0; border-bottom: 1.5px solid var(--rule);
    margin-bottom: 4px;
  }
</style>
</head>
<body>

<section class="card card-front" aria-label="Business card front">
  <svg class="front-swoosh" viewBox="0 0 800 457" preserveAspectRatio="none" aria-hidden="true">
    <defs>
      <linearGradient id="oliveBand" x1="0" y1="0" x2="1" y2="0">
        <stop offset="0" stop-color="#3a4808"/>
        <stop offset="1" stop-color="#2b3505"/>
      </linearGradient>
    </defs>
    <path d="M0 405 C 260 405, 560 380, 800 250 L 800 457 L 0 457 Z" fill="var(--peach)"/>
    <path d="M0 415 C 260 415, 560 395, 800 268 L 800 457 L 0 457 Z" fill="url(#oliveBand)"/>
    <path d="M120 395 C 380 392, 640 340, 800 200" fill="none" stroke="var(--lime)" stroke-width="6"/>
  </svg>

  <div class="front-brand">
    <span class="brand-dot"></span>
    <span class="brand-name">Bright Meadows</span>
  </div>

  <div class="divider"></div>

  <div class="contact">
    <p class="person">Martin Avery | <span class="job">Job Title</span></p>
    <p class="address">Your address Goes Here, City,<br>Zip Code, Country Name</p>
    <ul>
      <li>
        <svg viewBox="0 0 14 14"><path d="M3 1 L5 1 L6 4 L4.5 5.2 C5.3 7 7 8.7 8.8 9.5 L10 8 L13 9 L13 11 C13 12 12 13 11 13 C5.5 13 1 8.5 1 3 C1 2 2 1 3 1 Z" fill="#e07b2a"/></svg>
        555-0142-3368
      </li>
      <li>
        <svg viewBox="0 0 14 14"><rect x="2" y="5" width="10" height="7" rx="1" fill="#e07b2a"/><rect x="4" y="1" width="6" height="5" fill="#e07b2a"/><rect x="4.5" y="7" width="5" height="1.2" fill="#fff"/></svg>
        555-0197-2604
      </li>
      <li>
        <svg viewBox="0 0 14 14"><rect x="1" y="3" width="12" height="8" rx="1" fill="#e07b2a"/><path d="M1.5 3.5 L7 8 L12.5 3.5" fill="none" stroke="#fff" stroke-width="1.2"/></svg>
        hello@brightmeadows.example
      </li>
    </ul>
  </div>

  <p class="front-web">www.brightmeadows.example</p>
</section>

<section class="card card-back" aria-label="Business card back">
  <div class="back-brand">
    <span class="brand-dot"></span>
    <span class="brand-name">Bright Meadows</span>
  </div>
  <p class="back-web">www.brightmeadows.example</p>

  <div class="appointments">
    <h2>Your Appointments</h2>
    <div class="appt-row">
      <div class="appt-field date">Date <span class="appt-line"></span></div>
      <div class="appt-field time">Time <span class="appt-line"></span></div>
    </div>
    <div class="appt-row">
      <div class="appt-field date">Date <span class="appt-line"></span></div>
      <div class="appt-field time">Time <span class="appt-line"></span></div>
    </div>
    <div class="appt-row">
      <div class="appt-field date">Date <span class="appt-line"></span></div>
      <div class="appt-field time">Time <span class="appt-line"></span></div>
    </div>
  </div>
</section>

</body>
</html>
```